Business card design Needed for new logo / Construction business, home extensions and new builds

We need a business card design using our new logo files which i will attach to this project :)

We are a small construction business specialising in home extensions, new builds and property development. We are very ambitious and would appreciate professional and elegant designs for our new business card.

Very serious about using the services on MakerQuarry and recently acquired our new logo from here :)

Please get involved, i will feedback when i can as i am very busy but can respond daily, thanks

Target Market(s)

People that want to build onto their houses, new building developments or adding too their existing property

Industry/Entity Type

Construction

Contact Information for Business Card

Renwick Tolliver Construction, Lionel Ashby (Managing Director), Tel 07822254961, email - info@renwick-tolliver, www.renwick-tolliver.co.uk

Colors

Designer to choose colors to be used in the design.

Requirements
Must have
• I like a deep grey on the back please. A lot of you have provided black from and back, try mixing things up a little. The black looks cool 😎 Thanks

```html
<!DOCTYPE html>
<html lang="en">
<head>
<meta charset="utf-8">
<title>Renwick Tolliver Construction – Business Card</title>
<link rel="stylesheet" href="https://fonts.googleapis.com/css2?family=Cinzel:wght@600&family=Lato:wght@400;700&display=swap">
<style>
  :root {
    --page: #262626;
    --card-black: #050505;
    --card-grey: #1c1c1c;
    --gold: #d69a2a;
    --gold-light: #fbd787;
    --gold-dark: #c0851c;
    --silver: #cfd1d4;
    --silver-dark: #8e9094;
    --text-grey: #a9abae;
    --text-light: #eeeeee;
  }
  * { margin: 0; padding: 0; box-sizing: border-box; }
  html, body { width: 1200px; height: 1200px; overflow: hidden; }
  body { background: var(--page); position: relative; font-family: "Lato", sans-serif; }

  .card {
    position: absolute;
    left: 250px;
    width: 700px;
    height: 400px;
    border-radius: 20px;
    overflow: hidden;
  }
  .card--front {
    top: 170px;
    background: radial-gradient(ellipse at 55% 40%, #1d1d1d 0%, var(--card-black) 65%);
  }
  .card--back {
    top: 631px;
    background: radial-gradient(ellipse at 45% 45%, #2a2a2a 0%, var(--card-grey) 55%, #0d0d0d 100%);
  }

  /* brand */
  .brand-mark {
    position: absolute;
    width: 34px; height: 34px;
    background: var(--gold);
  }
  .card--front .brand-mark { left: 333px; top: 90px; }
  .brand-name {
    position: absolute;
    font-family: "Cinzel", serif;
    font-weight: 600;
    color: var(--silver);
    text-transform: uppercase;
    line-height: 1;
  }
  .card--front .brand-name { left: 0; width: 100%; top: 188px; text-align: center; }
  .brand-name__company { display: block; font-size: 27px; letter-spacing: 0.5px; }
  .brand-name__trade { display: inline-block; font-size: 19px; margin-top: 8px; letter-spacing: 0.5px; position: relative; }
  .brand-name__trade::before,
  .brand-name__trade::after {
    content: ""; position: absolute; top: 50%; width: 30px; height: 2px; background: var(--gold);
  }
  .brand-name__trade::before { right: calc(100% + 12px); }
  .brand-name__trade::after { left: calc(100% + 12px); }

  /* contact */
  .person { position: absolute; right: 390px; top: 267px; text-align: right; }
  .person__name { font-size: 27px; color: var(--gold); font-weight: 400; line-height: 1.1; }
  .person__role { font-size: 19px; color: var(--text-grey); margin-top: 4px; }
  .divider { position: absolute; left: 334px; top: 275px; width: 2px; height: 40px; background: var(--gold); }
  .contact { position: absolute; left: 355px; top: 270px; list-style: none; }
  .contact__item { display: flex; align-items: center; color: var(--text-light); height: 27px; }
  .contact__item svg { width: 15px; height: 15px; margin-right: 12px; fill: var(--gold); flex: none; }
  .contact__item--phone { font-size: 19px; letter-spacing: 0.5px; }
  .contact__item--email { font-size: 15.5px; }

  .web-band { position: absolute; left: 0; bottom: 0; width: 700px; height: 37px; }
  .web-band__text {
    position: absolute; left: 0; width: 646px; bottom: 0; height: 37px;
    display: flex; align-items: center; justify-content: center;
    font-size: 15px; letter-spacing: 2.4px; color: #1a1408;
  }
  .web-band__text b { font-weight: 700; }

  /* back */
  .back-brand { position: absolute; right: 33px; top: 290px; text-align: center; width: 320px; }
  .back-brand .brand-name { position: static; }
  .back-brand .brand-name__company { font-size: 25px; }
  .back-brand .brand-name__trade { font-size: 19px; }
  .back-brand .brand-mark { position: absolute; left: -46px; top: 2px; width: 28px; height: 28px; }
  .back-web {
    margin-top: 12px; font-size: 14.5px; letter-spacing: 2px; color: var(--gold);
  }
  .back-web b { font-weight: 700; }
</style>
</head>
<body>

<section class="card card--front" aria-label="Business card front">
  <span class="brand-mark" aria-hidden="true"></span>
  <h1 class="brand-name">
    <span class="brand-name__company">Renwick Tolliver</span>
    <span class="brand-name__trade">Construction</span>
  </h1>

  <div class="person">
    <p class="person__name">Lionel Ashby</p>
    <p class="person__role">Managing Director</p>
  </div>
  <span class="divider" aria-hidden="true"></span>
  <ul class="contact">
    <li class="contact__item contact__item--phone">
      <svg viewBox="0 0 24 24" aria-hidden="true"><path d="M6.6 10.8a15.1 15.1 0 0 0 6.6 6.6l2.2-2.2a1 1 0 0 1 1-.25 11.4 11.4 0 0 0 3.6.57 1 1 0 0 1 1 1V20a1 1 0 0 1-1 1A17 17 0 0 1 3 4a1 1 0 0 1 1-1h3.5a1 1 0 0 1 1 1c0 1.25.2 2.45.57 3.57a1 1 0 0 1-.25 1z"/></svg>
      07822254961
    </li>
    <li class="contact__item contact__item--email">
      <svg viewBox="0 0 24 24" aria-hidden="true"><path d="M2 5h20v14H2z M3.5 6.5 12 13l8.5-6.5" fill="var(--gold)"/><path d="M3 6.5 12 13.2 21 6.5" fill="none" stroke="#050505" stroke-width="1.6"/></svg>
      info@renwick-tolliver.co.uk
    </li>
  </ul>

  <svg class="web-band" viewBox="0 0 700 37" aria-hidden="true">
    <defs>
      <linearGradient id="band-gold" x1="0" x2="1" y1="0" y2="0">
        <stop offset="0" stop-color="var(--gold-dark)"/>
        <stop offset="0.45" stop-color="var(--gold-light)"/>
        <stop offset="0.85" stop-color="var(--gold-light)"/>
        <stop offset="1" stop-color="var(--gold)"/>
      </linearGradient>
      <linearGradient id="band-silver" x1="0" x2="1" y1="0" y2="0">
        <stop offset="0" stop-color="var(--silver-dark)"/>
        <stop offset="0.6" stop-color="#e3e4e6"/>
        <stop offset="1" stop-color="var(--silver)"/>
      </linearGradient>
    </defs>
    <rect x="0" y="0" width="700" height="37" fill="url(#band-silver)"/>
    <polygon points="0,0 588,0 615,37 0,37" fill="url(#band-gold)"/>
    <polygon points="588,0 600,0 627,37 615,37" fill="var(--gold)"/>
    <polygon points="600,0 612,0 640,37 627,37" fill="#050505"/>
  </svg>
  <p class="web-band__text">WWW.<b>RENWICK-TOLLIVER</b>.CO.UK</p>
</section>

<section class="card card--back" aria-label="Business card back">
  <div class="back-brand">
    <span class="brand-mark" aria-hidden="true"></span>
    <h2 class="brand-name">
      <span class="brand-name__company">Renwick Tolliver</span>
      <span class="brand-name__trade">Construction</span>
    </h2>
    <p class="back-web">WWW.<b>RENWICK-TOLLIVER</b>.CO.UK</p>
  </div>
</section>

</body>
</html>
```